University Student Business Card

Looking for a professional university student business card. Student is studying business with a focus on marketing. Some combination using a monogram and/or full name on the front with full name, university details and contact information on the back. Card should be modern design for a young professional. Prefer use of royal blue, black and white but am open to other uses of colour palette if it reinforces young/trendy style. Initials for a monogram are: KR. Full details will be provided in private consultation with designer(s).

Target Market(s)

Professional business people, marketers, advertisers, consultants

Industry/Entity Type

Business, marketing

Contact Information for Business Card

Monogram or personal logo, full name, university name, program of study, phone number, email address, pathfolio address

Other font styles liked:
• Open to suggestion to fulfill above requirements

Colors
0054AA
0677BA
7BADD7
CADEEF
E8F1F8

Requirements
Must have
• Monogram using letters K and R, and incorporate the business card details listed in the brief (specific details including personal contact info will be shared with successful designer to ensure privacy)
Nice to have
• Personal brand using monogram or personal logo (not a business logo)

```html
<!DOCTYPE html>
<html lang="en">
<head>
<meta charset="UTF-8">
<title>KR Student Business Card</title>
<link href="https://fonts.googleapis.com/css2?family=Lato:wght@400;700;900&display=swap" rel="stylesheet">
<style>
  :root {
    --navy: #021530;
    --royal: #0054AA;
    --white: #ffffff;
    --ink: #1a1a1a;
    --backdrop: #e6e9ee;
    --divider: #8a93a3;
  }
  * { margin: 0; padding: 0; box-sizing: border-box; }
  html, body {
    width: 1200px; height: 900px; overflow: hidden;
    background: var(--backdrop);
    font-family: "Lato", Arial, sans-serif;
  }
  .canvas {
    width: 1200px; height: 900px;
    display: flex; flex-direction: column; align-items: center; justify-content: center;
    gap: 28px;
  }
  .card {
    position: relative;
    width: 660px; height: 377px;
    overflow: hidden;
    box-shadow: 0 6px 18px rgba(0,0,0,0.18);
  }
  /* Front */
  .card-front {
    background: var(--navy);
    color: var(--white);
    display: flex; flex-direction: column; align-items: center;
  }
  .monogram {
    font-weight: 900;
    font-size: 120px;
    line-height: 1;
    letter-spacing: 4px;
    margin-top: 56px;
    color: var(--white);
  }
  .holder-name {
    margin-top: 34px;
    font-weight: 700;
    font-size: 26px;
    letter-spacing: 1px;
    color: var(--royal);
    text-transform: uppercase;
  }
  .holder-role {
    font-size: 17px;
    letter-spacing: 0.5px;
    margin-top: 2px;
  }
  .front-divider {
    width: 130px; height: 1px;
    background: var(--divider);
    margin: 14px 0 16px;
  }
  .profile-link {
    display: flex; align-items: center; gap: 10px;
    font-size: 18px;
    letter-spacing: 0.5px;
  }
  .profile-dot {
    width: 26px; height: 26px; border-radius: 50%;
    background: var(--royal);
  }
  /* Back */
  .card-back { background: var(--white); color: var(--ink); }
  .back-wave { position: absolute; inset: 0; }
  .back-content { position: absolute; left: 58px; top: 46px; z-index: 1; }
  .university-name {
    font-weight: 900;
    font-size: 31px;
    line-height: 38px;
    letter-spacing: 1px;
    color: var(--royal);
    text-transform: uppercase;
  }
  .address {
    margin-top: 28px;
    font-size: 17px;
    line-height: 22px;
    letter-spacing: 0.5px;
  }
  .contact-list {
    list-style: none;
    margin-top: 22px;
    font-size: 17px;
    line-height: 24px;
    letter-spacing: 0.5px;
  }
  .contact-list li { display: flex; align-items: center; gap: 12px; }
  .contact-icon { width: 18px; height: 18px; flex: none; }
  .back-monogram {
    position: absolute;
    right: 58px; top: 40px;
    font-weight: 900;
    font-size: 90px;
    line-height: 1;
    letter-spacing: 3px;
    color: var(--navy);
  }
</style>
</head>
<body>
<main class="canvas">

  <section class="card card-front" aria-label="Card front">
    <div class="monogram">KR</div>
    <h1 class="holder-name">Marcus Holland</h1>
    <p class="holder-role">Business Marketing</p>
    <div class="front-divider"></div>
    <p class="profile-link"><span class="profile-dot"></span>pathfolio.com/name</p>
  </section>

  <section class="card card-back" aria-label="Card back">
    <svg class="back-wave" viewBox="0 0 660 377" preserveAspectRatio="none" aria-hidden="true">
      <path fill="var(--royal)" d="M0,278 C200,278 370,254 492,206 L497,209 C380,270 210,296 0,296 Z"/>
      <path fill="var(--navy)" stroke="var(--white)" stroke-width="4"
            d="M-4,303 C220,303 380,272 500,226 C570,200 620,194 664,190 L664,381 L-4,381 Z"/>
    </svg>

    <div class="back-content">
      <h2 class="university-name">University Name</h2>
      <p class="address">87, Harbour Lane Street<br>30218, Northland</p>
      <ul class="contact-list">
        <li>
          <svg class="contact-icon" viewBox="0 0 24 24" aria-hidden="true">
            <path fill="var(--royal)" d="M6.6 10.8c1.4 2.8 3.8 5.1 6.6 6.6l2.2-2.2c.3-.3.7-.4 1-.2 1.1.4 2.3.6 3.6.6.6 0 1 .4 1 1V20c0 .6-.4 1-1 1C10.6 21 3 13.4 3 4c0-.6.4-1 1-1h3.5c.6 0 1 .4 1 1 0 1.3.2 2.5.6 3.6.1.3 0 .7-.2 1z"/>
          </svg>
          055-987 321 640
        </li>
        <li>
          <svg class="contact-icon" viewBox="0 0 24 24" aria-hidden="true">
            <rect x="2" y="5" width="20" height="14" fill="var(--royal)"/>
            <polyline points="2,5 12,13 22,5" fill="none" stroke="var(--white)" stroke-width="1.6"/>
          </svg>
          hello@kestrelmail.com
        </li>
        <li>
          <svg class="contact-icon" viewBox="0 0 24 24" aria-hidden="true">
            <g fill="none" stroke="var(--royal)" stroke-width="1.8">
              <circle cx="12" cy="12" r="9.5"/>
              <ellipse cx="12" cy="12" rx="4.5" ry="9.5"/>
              <line x1="2.5" y1="12" x2="21.5" y2="12"/>
              <line x1="4" y1="7" x2="20" y2="7"/>
              <line x1="4" y1="17" x2="20" y2="17"/>
            </g>
          </svg>
          www.kestrelstudio.com
        </li>
      </ul>
    </div>

    <div class="back-monogram">KR</div>
  </section>

</main>
</body>
</html>
```